KDWB Business Card

Looking for a business card design to incorporate our branding. We want to only use the colors listing in the Branding Package (attached).
Updates

Target Market(s)

People who need their phone or device fixed.

Industry/Entity Type

Electronics

Contact Information for Business Card

Please use:

Brightwick Gadget Clinic LLC
4810 E Harlow Ridge Rd
Suite 417
San Antonio, TX 78163

Marcus Delgrove, Store Manager

(210) 555-0147

Requirements
Must have
• Must include the colors that are contained within the Branding Package PDF file.

```html
<!DOCTYPE html>
<html lang="en">
<head>
<meta charset="utf-8">
<title>Brightwick Gadget Clinic – Business Card</title>
<link rel="stylesheet" href="https://fonts.googleapis.com/css2?family=Arimo:wght@400;700&display=swap">
<style>
  :root {
    --bg: #e9e6e1;
    --paper: #ffffff;
    --ink: #3a3a3c;
    --orange: #ea4e1b;
    --band: #4a4b4f;
    --band-text: #e4e4e4;
    --night: #222224;
  }
  * { margin: 0; padding: 0; box-sizing: border-box; }
  html, body { width: 1200px; height: 892px; overflow: hidden; }
  body {
    background: var(--bg);
    font-family: "Arimo", Arial, sans-serif;
    position: relative;
  }
  .card {
    position: absolute;
    width: 560px;
    height: 320px;
    border-radius: 4px;
    overflow: hidden;
    box-shadow: 0 8px 24px rgba(0,0,0,.18);
  }
  .card-front { left: 90px; top: 110px; background: var(--paper); }
  .card-back { left: 550px; top: 462px; background: var(--night); }

  .wordmark {
    position: absolute;
    display: flex;
    align-items: center;
    gap: 10px;
    color: var(--orange);
    font-weight: 400;
    white-space: nowrap;
  }
  .wordmark .mark-square {
    width: 30px; height: 30px;
    background: var(--orange);
    border-radius: 6px;
    flex: none;
  }
  .card-front .wordmark { left: 26px; top: 96px; font-size: 18px; }
  .card-back .wordmark {
    left: 50%; top: 50%;
    transform: translate(-50%, -50%);
    font-size: 30px;
  }
  .card-back .wordmark .mark-square { width: 44px; height: 44px; border-radius: 8px; }

  .divider {
    position: absolute;
    left: 300px; top: 40px;
    width: 1.5px; height: 116px;
    background: var(--ink);
  }
  .contact { position: absolute; left: 316px; top: 38px; color: var(--ink); }
  .contact .person-name { font-size: 23px; line-height: 1.1; }
  .contact .person-title { font-size: 12px; color: var(--orange); margin-top: 2px; }
  .contact ul { list-style: none; margin-top: 16px; }
  .contact li {
    display: flex; align-items: center; gap: 8px;
    font-size: 12.5px; line-height: 1.65;
  }
  .contact .icon {
    width: 11px; height: 11px;
    background: var(--orange);
    display: inline-flex; align-items: center; justify-content: center;
  }
  .band { position: absolute; left: 0; bottom: 0; width: 560px; height: 130px; }
  .address {
    position: absolute;
    left: 0; right: 0; bottom: 12px;
    text-align: center;
    color: var(--band-text);
    font-size: 12px;
    line-height: 14px;
    letter-spacing: .2px;
  }
</style>
</head>
<body>

<section class="card card-front">
  <div class="wordmark"><span class="mark-square"></span>Brightwick Gadget Clinic</div>

  <div class="divider"></div>
  <div class="contact">
    <p class="person-name">Marcus Delgrove</p>
    <p class="person-title">Store Manager</p>
    <ul>
      <li><span class="icon"><svg width="7" height="7" viewBox="0 0 10 10"><path d="M2 1 L4 1 L4.5 3.5 L3.3 4.3 Q4.5 6.5 5.7 6.7 L6.5 5.5 L9 6 L9 8 Q5 9.5 1.5 4.5 Z" fill="#fff"/></svg></span>(210) 555-0147</li>
      <li><span class="icon"><svg width="7" height="7" viewBox="0 0 10 10"><rect x="1" y="2" width="8" height="6" fill="none" stroke="#fff" stroke-width="1.3"/><path d="M1 2 L5 5.5 L9 2" fill="none" stroke="#fff" stroke-width="1.3"/></svg></span>marcus@brightwickclinic.com</li>
      <li><span class="icon"><svg width="7" height="7" viewBox="0 0 10 10"><circle cx="5" cy="5" r="3.8" fill="none" stroke="#fff" stroke-width="1.3"/><path d="M1.2 5 H8.8" stroke="#fff" stroke-width="1"/></svg></span>www.brightwickclinic.com</li>
    </ul>
  </div>

  <svg class="band" viewBox="0 0 560 130" aria-hidden="true">
    <path d="M0 84 C 170 80 390 56 560 0 L560 16 C 392 70 172 92 0 92 Z" fill="var(--orange)"/>
    <path d="M0 98 C 180 94 400 68 560 22 L560 130 L0 130 Z" fill="var(--band)"/>
  </svg>
  <p class="address">4810 E Harlow Ridge Rd, Suite 417, San Antonio, TX 78163</p>
</section>

<section class="card card-back">
  <div class="wordmark"><span class="mark-square"></span>Brightwick Gadget Clinic</div>
</section>

</body>
</html>
```